Bright Path Notes Wordpress Blog

I need to design a WordPress blog page. The name of the Blog is "Bright Path Notes". I am hoping for a simple design that is easy for me to post future posts to. I like the color teal for this. The website is brightpathnotesblog.com where I am going to write a personal blog. I don't have a logo for this, but am hoping for a header that has some swirly, but classy looking text. Easy on the eyes. The website will only have a couple of pages - the home landing page, and an about me page.

Font styles to use
Script

Colors
00a990
86cfc6
cfeae6

Requirements
Must have
• A header for the landing page of the blog. Clean layout of where the blog posts will lie.

```html
<!DOCTYPE html>
<html lang="en">
<head>
<meta charset="utf-8">
<title>Bright Path Notes</title>
<link rel="stylesheet" href="https://fonts.googleapis.com/css2?family=Parisienne&family=Open+Sans:wght@400;600&display=swap">
<style>
:root{
  --page:#f5f9f8;
  --white:#ffffff;
  --ink:#333a3c;
  --ink-soft:#6b7476;
  --ink-faint:#9aa3a5;
  --heading:#2f3436;
  --teal:#00a990;
  --teal-deep:#00806d;
  --teal-mid:#86cfc6;
  --teal-pale:#cfeae6;
  --header-bg:#eef7f5;
  --line:#dde6e4;
  --footer:#2b2c2d;
  --footer-text:#d8dadb;
  --social:#c9463a;
  --social-blue:#3b6fb0;
  --social-sky:#2fa6dc;
  --social-pink:#d8478f;
}
*{box-sizing:border-box;margin:0;padding:0}
html,body{width:1200px;height:2590px;overflow:hidden}
body{position:relative;background:var(--page);font-family:"Open Sans",Arial,sans-serif;color:var(--ink)}
h2,h3,h4{font-weight:400}
.abs{position:absolute}

/* header */
.site-header{position:absolute;left:0;top:0;width:1200px;height:161px;background:var(--header-bg)}
.header-band{position:absolute;left:88px;top:50px;width:1024px;height:56px;background:var(--teal-pale);border-top:2px solid var(--teal-mid);border-bottom:2px solid var(--teal-mid)}
.corner-ornament{position:absolute;top:0;width:88px;height:150px;background:linear-gradient(180deg,var(--teal-mid),var(--teal-pale))}
.site-title{position:absolute;left:112px;top:50px;font-family:"Parisienne",cursive;font-weight:400;font-size:40px;line-height:56px;color:var(--teal-deep)}
.main-nav{position:absolute;left:666px;top:60px;display:flex;align-items:center}
.main-nav a{font-size:16px;color:var(--heading);text-decoration:none;text-transform:uppercase;height:36px;line-height:36px}
.main-nav .current{background:var(--white);color:var(--teal-deep);border-radius:18px;padding:0 24px;margin-right:38px}
.main-nav .about{margin-right:62px}

/* hero */
.hero{position:absolute;left:0;top:161px;width:1200px;height:514px;background:linear-gradient(160deg,#c9b79a 0%,#f0c27f 45%,#c98a3e 75%,#5a4a2f 100%)}
.hero-title{position:absolute;right:87px;top:200px;font-family:"Parisienne",cursive;font-weight:400;font-size:58px;color:#3d4346;line-height:1}
.hero-sub{position:absolute;right:87px;top:266px;font-size:23px;font-weight:600;color:#3d4043}
.hero-arrows{position:absolute;left:1055px;top:325px;display:flex;gap:4px}

/* section headings */
.section-title{position:absolute;font-size:31px;color:var(--heading);text-transform:uppercase}
.block-title{position:absolute;font-size:20px;color:var(--heading);text-transform:uppercase}

/* blog cards */
.post-card{position:absolute;left:88px;width:691px;height:239px;background:var(--white);border:1px solid var(--line)}
.post-thumb{position:absolute;left:16px;top:26px;width:216px;height:187px}
.post-body{position:absolute;left:245px;top:26px;width:428px}
.post-title{font-size:17px;color:#2b3133}
.post-meta{font-size:10.5px;color:var(--ink-soft);margin-top:9px}
.post-excerpt{font-size:13px;line-height:21px;color:var(--ink-soft);margin-top:12px;text-align:justify}
.post-actions{display:flex;align-items:center;margin-top:18px}
.btn-more{display:inline-block;width:93px;height:28px;line-height:28px;text-align:center;background:var(--teal);color:var(--white);font-size:10px;font-weight:600;text-transform:uppercase;margin-right:18px}
.share-dots{display:flex;gap:7px}
.share-dots span{width:21px;height:21px;border-radius:50%}

/* sidebar */
.search-panel{position:absolute;left:800px;top:792px;width:314px;height:78px;background:var(--teal-mid)}
.search-field{position:absolute;left:18px;top:19px;width:280px;height:40px;background:var(--white);border-radius:3px;font-size:11px;line-height:40px;padding-left:20px;color:var(--ink)}
.search-field svg{position:absolute;right:18px;top:14px}
.popular-list{position:absolute;left:800px;top:927px;width:314px;height:876px;background:var(--white);border-top:2px solid var(--teal-mid);border-left:1px solid var(--line);border-right:1px solid var(--line);border-bottom:1px solid var(--line)}
.popular-item{position:absolute;left:16px;width:282px;height:108px;border-bottom:1px solid var(--line)}
.popular-thumb{position:absolute;left:2px;top:14px;width:83px;height:72px}
.popular-text{position:absolute;left:99px;top:18px;font-size:12px;line-height:19px;color:#3b4143;width:168px}
.popular-icons{position:absolute;left:99px;top:64px;display:flex;gap:11px}

/* pagination */
.pagination{position:absolute;left:90px;top:1828px;display:flex;gap:10px}
.pagination span{height:24px;min-width:24px;line-height:22px;text-align:center;border:1px solid var(--line);background:var(--white);font-size:11px;color:var(--ink-soft);padding:0 6px}
.pagination .active{background:var(--teal);color:var(--white);border-color:var(--teal)}
.pagination .wide{width:52px}

/* articles */
.panel{position:absolute;background:var(--white);border:1px solid var(--line);border-top:3px solid var(--teal-mid)}
.article{position:absolute;top:32px;width:198px}
.article-thumb{width:198px;height:138px}
.article-text{font-size:13px;line-height:20px;color:#3b4143;margin-top:16px;width:185px}
.article-date{font-size:12px;color:var(--ink-soft);margin-top:26px;display:flex;align-items:center;gap:10px}
.video-thumb{position:absolute;left:16px;top:20px;width:274px;height:266px;background:linear-gradient(160deg,#c7a98a,#8e7a68 60%,#5d534a)}
.video-caption{position:absolute;left:22px;top:200px;font-size:16px;color:var(--white)}
.video-tag{position:absolute;left:22px;top:236px;font-size:10px;color:#eef0f0;display:flex;align-items:center;gap:8px}

/* footer */
.site-footer{position:absolute;left:0;top:2324px;width:1200px;height:266px;background:var(--footer);color:var(--footer-text)}
.footer-brand{position:absolute;left:93px;top:90px;font-family:"Parisienne",cursive;font-size:30px;color:var(--teal-mid)}
.footer-heading{position:absolute;top:44px;font-size:14px;color:var(--white);text-transform:uppercase}
.footer-copy{position:absolute;font-size:11.5px;line-height:22px;color:var(--footer-text)}
.signup{position:absolute;left:639px;top:118px;display:flex}
.signup .field{width:147px;height:28px;background:var(--white);font-size:11px;color:var(--ink-faint);line-height:28px;padding-left:8px}
.signup .send{width:56px;height:28px;background:var(--teal);color:var(--white);font-size:11px;line-height:28px;text-align:center}
.follow-icons{position:absolute;left:941px;top:90px;display:flex;gap:12px}
.follow-icons span{width:26px;height:26px;background:var(--white);border-radius:3px}
.footer-rule{position:absolute;left:93px;top:206px;width:1014px;height:1px;background:#444647}
.copyright{position:absolute;left:0;width:1200px;top:226px;text-align:center;font-size:12px;color:var(--footer-text)}
</style>
</head>
<body>

<header class="site-header">
  <div class="header-band"></div>
  <div class="corner-ornament" style="left:0" role="img" aria-label="Decorative scroll ornament"></div>
  <div class="corner-ornament" style="right:0" role="img" aria-label="Decorative scroll ornament"></div>
  <div class="site-title">Bright Path Notes</div>
  <nav class="main-nav">
    <a class="current" href="#">Home</a>
    <a class="about" href="#">About Nora</a>
    <a href="#">Contact</a>
  </nav>
</header>

<section class="hero" role="img" aria-label="Family flying a kite together in a field at sunset">
  <div class="hero-title">Bright Path Notes</div>
  <div class="hero-sub">Neque porro quisquam est qui dolorem</div>
  <div class="hero-arrows">
    <svg width="23" height="23" viewBox="0 0 23 23"><circle cx="11.5" cy="11.5" r="11.5" fill="#8d8f90"/><path d="M13.5 7l-4.5 4.5 4.5 4.5" stroke="#fff" stroke-width="2" fill="none"/></svg>
    <svg width="23" height="23" viewBox="0 0 23 23"><circle cx="11.5" cy="11.5" r="11.5" fill="#8d8f90"/><path d="M9.5 7l4.5 4.5-4.5 4.5" stroke="#fff" stroke-width="2" fill="none"/></svg>
  </div>
</section>

<h2 class="section-title" style="left:88px;top:728px">Latest Blogs</h2>

<article class="post-card" style="top:792px">
  <div class="post-thumb" style="background:linear-gradient(135deg,#d9c2ad,#a9836a)" role="img" aria-label="Smiling couple embracing"></div>
  <div class="post-body">
    <h3 class="post-title">Porro quisquam est qui dolorem ipsum</h3>
    <p class="post-meta">Author : admin &nbsp;|&nbsp; Post id : 12365 &nbsp;|&nbsp; Post on : October 1, 2017 &nbsp;|&nbsp; 5 Comments</p>
    <p class="post-excerpt">Sed id tincidunt arcu. Maecenas eget elit at purus dapibus dictum. Vestibulum ante ipsum primis in faucibus orci luctus et ultrices posuere cubilia Curae; In hac habitasse platea dictumst.</p>
    <div class="post-actions"><span class="btn-more">Learn More</span><div class="share-dots"><span style="background:var(--social-sky)"></span><span style="background:var(--social-blue)"></span><span style="background:var(--social)"></span><span style="background:var(--social-pink)"></span><span style="background:var(--social)"></span></div></div>
  </div>
</article>

<article class="post-card" style="top:1046px">
  <div class="post-thumb" style="background:linear-gradient(135deg,#4f6a3c,#b8643f 55%,#e6e2d6)" role="img" aria-label="Woman with red hair among white blossoms"></div>
  <div class="post-body">
    <h3 class="post-title">Dolorem ipsum quia dolor sit amet</h3>
    <p class="post-meta">Author : admin &nbsp;|&nbsp; Post id : 12365 &nbsp;|&nbsp; Post on : October 1, 2017 &nbsp;|&nbsp; 5 Comments</p>
    <p class="post-excerpt">Sed id tincidunt arcu. Maecenas eget elit at purus dapibus dictum. Vestibulum ante ipsum primis in faucibus orci luctus et ultrices posuere cubilia Curae; In hac habitasse platea dictumst.</p>
    <div class="post-actions"><span class="btn-more">Learn More</span><div class="share-dots"><span style="background:var(--social-sky)"></span><span style="background:var(--social-blue)"></span><span style="background:var(--social)"></span><span style="background:var(--social-pink)"></span><span style="background:var(--social)"></span></div></div>
  </div>
</article>

<article class="post-card" style="top:1305px">
  <div class="post-thumb" style="background:linear-gradient(135deg,#c9a884,#e8ddd0 50%,#7f8a96)" role="img" aria-label="Couple smiling while reviewing papers"></div>
  <div class="post-body">
    <h3 class="post-title">Neque porro quisquam est qui dolorem ipsum</h3>
    <p class="post-meta">Author : admin &nbsp;|&nbsp; Post id : 12365 &nbsp;|&nbsp; Post on : October 1, 2017 &nbsp;|&nbsp; 5 Comments</p>
    <p class="post-excerpt">Sed id tincidunt arcu. Maecenas eget elit at purus dapibus dictum. Vestibulum ante ipsum primis in faucibus orci luctus et ultrices posuere cubilia Curae; In hac habitasse platea dictumst.</p>
    <div class="post-actions"><span class="btn-more">Learn More</span><div class="share-dots"><span style="background:var(--social-sky)"></span><span style="background:var(--social-blue)"></span><span style="background:var(--social)"></span><span style="background:var(--social-pink)"></span><span style="background:var(--social)"></span></div></div>
  </div>
</article>

<article class="post-card" style="top:1564px">
  <div class="post-thumb" style="background:linear-gradient(180deg,#8fa6c0,#c9c7b2 55%,#8a8a3a)" role="img" aria-label="Woman with open arms in a meadow"></div>
  <div class="post-body">
    <h3 class="post-title">Quisquam est qui dolorem ipsum</h3>
    <p class="post-meta">Author : admin &nbsp;|&nbsp; Post id : 12365 &nbsp;|&nbsp; Post on : October 1, 2017 &nbsp;|&nbsp; 5 Comments</p>
    <p class="post-excerpt">Sed id tincidunt arcu. Maecenas eget elit at purus dapibus dictum. Vestibulum ante ipsum primis in faucibus orci luctus et ultrices posuere cubilia Curae; In hac habitasse platea dictumst.</p>
    <div class="post-actions"><span class="btn-more">Learn More</span><div class="share-dots"><span style="background:var(--social-sky)"></span><span style="background:var(--social-blue)"></span><span style="background:var(--social)"></span><span style="background:var(--social-pink)"></span><span style="background:var(--social)"></span></div></div>
  </div>
</article>

<div class="pagination">
  <span class="wide">Prev</span><span class="active">1</span><span>2</span><span>3</span><span>4</span><span>5</span><span>6</span><span>...</span><span>22</span><span class="wide">Next</span>
</div>

<aside>
  <div class="search-panel">
    <div class="search-field">SEARCH
      <svg width="12" height="12" viewBox="0 0 12 12"><circle cx="5" cy="5" r="3.6" stroke="#333" stroke-width="1.6" fill="none"/><path d="M7.6 7.6L11 11" stroke="#333" stroke-width="1.6"/></svg>
    </div>
  </div>
  <h3 class="block-title" style="left:800px;top:893px">Popular Posts</h3>
  <div class="popular-list">
    <div class="popular-item" style="top:0"><div class="popular-thumb" style="background:linear-gradient(135deg,#6f9a5a,#c8b79a)" role="img" aria-label="Older couple walking outdoors"></div><p class="popular-text">Ipsum is simply dummy text of the printing and type</p><div class="popular-icons"><svg width="12" height="12"><path d="M6 1l1.5 3.2 3.5.4-2.6 2.4.7 3.5L6 8.8 2.9 10.5l.7-3.5L1 4.6l3.5-.4z" fill="none" stroke="#999"/></svg><svg width="12" height="12"><rect x="1" y="2" width="10" height="9" fill="none" stroke="#999"/></svg><svg width="12" height="12"><circle cx="6" cy="4" r="2.5" fill="none" stroke="#999"/><path d="M1.5 11c1-3 8-3 9 0" fill="none" stroke="#999"/></svg></div></div>
    <div class="popular-item" style="top:108px"><div class="popular-thumb" style="background:linear-gradient(135deg,#d6b48d,#8fa86a)" role="img" aria-label="Family smiling outdoors"></div><p class="popular-text">Ipsum is simply dummy text of the printing and type</p><div class="popular-icons"><svg width="12" height="12"><rect x="1" y="2" width="10" height="9" fill="none" stroke="#999"/></svg><svg width="12" height="12"><circle cx="6" cy="4" r="2.5" fill="none" stroke="#999"/><path d="M1.5 11c1-3 8-3 9 0" fill="none" stroke="#999"/></svg><svg width="12" height="12"><rect x="1" y="2" width="10" height="7" fill="none" stroke="#999"/><path d="M4 9l-1 2.5L6 9" fill="none" stroke="#999"/></svg></div></div>
    <div class="popular-item" style="top:216px"><div class="popular-thumb" style="background:linear-gradient(135deg,#e3d8cc,#b49a84)" role="img" aria-label="Couple relaxing together"></div><p class="popular-text">Ipsum is simply dummy text of the printing and type</p><div class="popular-icons"><svg width="12" height="12"><path d="M6 1l1.5 3.2 3.5.4-2.6 2.4.7 3.5L6 8.8 2.9 10.5l.7-3.5L1 4.6l3.5-.4z" fill="none" stroke="#999"/></svg><svg width="12" height="12"><rect x="1" y="2" width="10" height="9" fill="none" stroke="#999"/></svg><svg width="12" height="12"><circle cx="6" cy="4" r="2.5" fill="none" stroke="#999"/><path d="M1.5 11c1-3 8-3 9 0" fill="none" stroke="#999"/></svg><svg width="12" height="12"><rect x="1" y="2" width="10" height="7" fill="none" stroke="#999"/><path d="M4 9l-1 2.5L6 9" fill="none" stroke="#999"/></svg></div></div>
    <div class="popular-item" style="top:324px"><div class="popular-thumb" style="background:linear-gradient(135deg,#c9a36b,#7d8f5a)" role="img" aria-label="Family playing in a park"></div><p class="popular-text">Ipsum is simply dummy text of the printing and type</p><div class="popular-icons"><svg width="12" height="12"><rect x="1" y="2" width="10" height="9" fill="none" stroke="#999"/></svg><svg width="12" height="12"><circle cx="6" cy="4" r="2.5" fill="none" stroke="#999"/><path d="M1.5 11c1-3 8-3 9 0" fill="none" stroke="#999"/></svg><svg width="12" height="12"><rect x="1" y="2" width="10" height="7" fill="none" stroke="#999"/><path d="M4 9l-1 2.5L6 9" fill="none" stroke="#999"/></svg></div></div>
    <div class="popular-item" style="top:432px"><div class="popular-thumb" style="background:linear-gradient(135deg,#d8cfc4,#8a7868)" role="img" aria-label="Couple sitting together at home"></div><p class="popular-text">Ipsum is simply dummy text of the printing and type</p><div class="popular-icons"><svg width="12" height="12"><rect x="1" y="2" width="10" height="9" fill="none" stroke="#999"/></svg><svg width="12" height="12"><circle cx="6" cy="4" r="2.5" fill="none" stroke="#999"/><path d="M1.5 11c1-3 8-3 9 0" fill="none" stroke="#999"/></svg><svg width="12" height="12"><rect x="1" y="2" width="10" height="7" fill="none" stroke="#999"/><path d="M4 9l-1 2.5L6 9" fill="none" stroke="#999"/></svg></div></div>
    <div class="popular-item" style="top:540px"><div class="popular-thumb" style="background:linear-gradient(135deg,#7fa0b8,#e5e1da)" role="img" aria-label="Man smiling by a window"></div><p class="popular-text">Ipsum is simply dummy text of the printing and type</p><div class="popular-icons"><svg width="12" height="12"><rect x="1" y="2" width="10" height="9" fill="none" stroke="#999"/></svg><svg width="12" height="12"><circle cx="6" cy="4" r="2.5" fill="none" stroke="#999"/><path d="M1.5 11c1-3 8-3 9 0" fill="none" stroke="#999"/></svg><svg width="12" height="12"><rect x="1" y="2" width="10" height="7" fill="none" stroke="#999"/><path d="M4 9l-1 2.5L6 9" fill="none" stroke="#999"/></svg></div></div>
    <div class="popular-item" style="top:648px"><div class="popular-thumb" style="background:linear-gradient(135deg,#8a6a55,#c9b2a0)" role="img" aria-label="Man gesturing while talking"></div><p class="popular-text">Ipsum is simply dummy text of the printing and type</p><div class="popular-icons"><svg width="12" height="12"><rect x="1" y="2" width="10" height="9" fill="none" stroke="#999"/></svg><svg width="12" height="12"><circle cx="6" cy="4" r="2.5" fill="none" stroke="#999"/><path d="M1.5 11c1-3 8-3 9 0" fill="none" stroke="#999"/></svg><svg width="12" height="12"><rect x="1" y="2" width="10" height="7" fill="none" stroke="#999"/><path d="M4 9l-1 2.5L6 9" fill="none" stroke="#999"/></svg></div></div>
    <div class="popular-item" style="top:756px;border-bottom:none"><div class="popular-thumb" style="background:linear-gradient(135deg,#d9d2c8,#9c7c6a)" role="img" aria-label="Woman smiling at a desk"></div><p class="popular-text">Ipsum is simply dummy text of the printing and type</p><div class="popular-icons"><svg width="12" height="12"><rect x="1" y="2" width="10" height="9" fill="none" stroke="#999"/></svg><svg width="12" height="12"><circle cx="6" cy="4" r="2.5" fill="none" stroke="#999"/><path d="M1.5 11c1-3 8-3 9 0" fill="none" stroke="#999"/></svg><svg width="12" height="12"><rect x="1" y="2" width="10" height="7" fill="none" stroke="#999"/><path d="M4 9l-1 2.5L6 9" fill="none" stroke="#999"/></svg></div></div>
  </div>
</aside>

<h3 class="block-title" style="left:93px;top:1913px">Latest Articles</h3>
<svg class="abs" style="left:737px;top:1922px" width="36" height="8"><circle cx="4" cy="4" r="3" fill="#c9cfd0"/><circle cx="18" cy="4" r="3" fill="#00a990"/><circle cx="32" cy="4" r="3" fill="#c9cfd0"/></svg>
<section class="panel" style="left:92px;top:1956px;width:690px;height:309px">
  <div class="article" style="left:23px"><div class="article-thumb" style="background:linear-gradient(135deg,#c99a6a,#e6d8c6)" role="img" aria-label="Two women reading together"></div><p class="article-text">Ipsum is simply dummy text of the printing and type</p><p class="article-date"><svg width="12" height="11"><rect x=".5" y="1.5" width="11" height="9" fill="none" stroke="#999"/></svg>27 March, 2017</p></div>
  <div class="article" style="left:244px"><div class="article-thumb" style="background:linear-gradient(135deg,#e8e4dc,#8f7f70)" role="img" aria-label="Family gathered around a table"></div><p class="article-text">Ipsum is simply dummy text of the printing and type</p><p class="article-date"><svg width="12" height="11"><rect x=".5" y="1.5" width="11" height="9" fill="none" stroke="#999"/></svg>7 March, 2017</p></div>
  <div class="article" style="left:464px"><div class="article-thumb" style="background:linear-gradient(135deg,#f0ece6,#b58f74)" role="img" aria-label="Couple working at a laptop"></div><p class="article-text">Ipsum is simply dummy text of the printing and type</p><p class="article-date"><svg width="12" height="11"><rect x=".5" y="1.5" width="11" height="9" fill="none" stroke="#999"/></svg>1 January, 2017</p></div>
</section>

<h3 class="block-title" style="left:803px;top:1913px">Videos</h3>
<svg class="abs" style="left:1086px;top:1918px" width="22" height="14"><path d="M7 2L2 7l5 5M15 2l5 5-5 5" stroke="#4a5355" stroke-width="1.6" fill="none"/></svg>
<section class="panel" style="left:803px;top:1956px;width:309px;height:309px">
  <div class="video-thumb" role="img" aria-label="Family reading a book together">
    <svg class="abs" style="left:117px;top:82px" width="40" height="40"><circle cx="20" cy="20" r="20" fill="#3a3d3f" opacity=".8"/><path d="M16 12l12 8-12 8z" fill="#fff"/></svg>
    <p class="video-caption">Porro quisquam est, qui sum</p>
    <p class="video-tag"><svg width="12" height="10"><path d="M.5 1.5h4l1 1.5h6v6.5H.5z" fill="none" stroke="#eee"/></svg>Cleaning</p>
  </div>
</section>

<footer class="site-footer">
  <div class="footer-brand">Bright Path Notes</div>
  <h4 class="footer-heading" style="left:359px">Contact Us</h4>
  <p class="footer-copy" style="left:359px;top:80px">Address : 12 Linden Row, Harbour Side<br>Kelmford, KF4 2LP<br>Phone : +44 20 5550 1937<br>Email : hello@brightpathnotesblog.com</p>
  <h4 class="footer-heading" style="left:639px">Join Our Mailing List</h4>
  <p class="footer-copy" style="left:639px;top:76px;width:210px;line-height:18px">Your about us information would fit here nicely.</p>
  <div class="signup"><span class="field">Email address</span><span class="send">Submit</span></div>
  <h4 class="footer-heading" style="left:941px">Follow Us Out There</h4>
  <div class="follow-icons"><span></span><span></span><span></span><span></span></div>
  <div class="footer-rule"></div>
  <p class="copyright">Copyright © 2017. All Rights Reserved</p>
</footer>

</body>
</html>
```